Q&J RESTORATION

I want a brochure similiar to the example i've attached.
My company name is Q&J Restoration. The website is: Q-J-Restoration.example.
The phone number is 919.555.0147.

I don't like the "yellow" being the main color of the example so I'm open to suggestions. I want something CLEAN & Simple, like our logo . This will be a bi fold brochure

```html
<!DOCTYPE html>
<html lang="en">
<head>
<meta charset="utf-8">
<title>Q&amp;J Restoration – Bi-fold Brochure Concept</title>
<link rel="stylesheet" href="https://fonts.googleapis.com/css2?family=Montserrat:wght@400;500;600;700&display=swap">
<style>
  :root{
    --board:#6e6e6e;
    --paper:#e9eaee;
    --paper-deep:#e2e3e7;
    --blue:#2a8bd4;
    --blue-deep:#0a66b8;
    --navy:#114a8c;
    --ink:#1b4f8f;
    --cyan:#22b8ee;
    --label:#1d1d1d;
    --white:#ffffff;
  }
  *{margin:0;padding:0;box-sizing:border-box;}
  html,body{width:971px;height:1200px;overflow:hidden;background:var(--board);}
  body{font-family:"Montserrat",Arial,sans-serif;}
  .board{position:absolute;left:0;top:0;width:1736px;height:2146px;transform:scale(0.55933);transform-origin:0 0;background:var(--board);}
  .art{position:absolute;left:0;top:0;}
  .abs{position:absolute;}
  .side-label{position:absolute;writing-mode:vertical-rl;transform:rotate(180deg);font-size:21px;letter-spacing:1px;color:var(--label);}
  .caption{position:absolute;left:0;width:1654px;top:2030px;text-align:center;font-size:23px;letter-spacing:.5px;color:var(--label);}

  /* back panel */
  .contact{position:absolute;left:392px;width:250px;top:692px;text-align:center;color:var(--ink);}
  .contact-title{font-size:27px;font-weight:700;color:#2a7fc6;}
  .contact-rule{position:relative;height:2px;background:#9aa7b8;margin:8px 10px 0;}
  .contact-rule span{position:absolute;left:57px;top:-2px;width:61px;height:5px;border-radius:3px;background:var(--blue);}
  .contact-icons{display:flex;justify-content:center;gap:6px;margin-top:16px;}
  .contact-icons svg{width:22px;height:22px;}
  .contact-phone{font-size:26px;font-weight:700;margin-top:13px;color:var(--ink);}
  .contact-web{font-size:16.5px;margin-top:6px;color:var(--ink);white-space:nowrap;margin-left:-30px;margin-right:-30px;}
  .contact-web b{font-weight:700;}
  .contact-address{font-size:12.5px;line-height:16px;margin-top:6px;color:var(--ink);white-space:nowrap;margin-left:-30px;margin-right:-30px;}
  .wordmark{position:absolute;display:flex;align-items:center;gap:12px;font-weight:600;white-space:nowrap;}
  .wordmark .mark-square{display:inline-block;}
  .wordmark--back{left:405px;top:930px;font-size:34px;color:var(--navy);}
  .wordmark--back .mark-square{width:16px;height:16px;background:var(--navy);}
  .wordmark--front{left:930px;top:586px;font-size:54px;color:var(--white);}
  .wordmark--front .mark-square{width:24px;height:24px;background:var(--white);}
  .wordmark--inner{left:1250px;top:1608px;font-size:31px;color:var(--navy);}
  .wordmark--inner .mark-square{width:15px;height:15px;background:var(--navy);}

  /* front panel */
  .front-tagline{position:absolute;left:980px;width:466px;top:848px;text-align:center;font-size:38px;line-height:42px;font-weight:400;color:#2a7fc6;letter-spacing:.5px;}
  .front-web{position:absolute;left:1032px;top:954px;width:372px;height:42px;border:1.5px solid var(--navy);display:flex;align-items:center;justify-content:center;font-size:23px;color:var(--ink);white-space:nowrap;}
  .front-web b{font-weight:700;}

  /* inner right */
  .inner-head{position:absolute;left:900px;width:636px;top:1133px;text-align:center;color:var(--ink);}
  .inner-head h2{font-size:34px;line-height:40px;font-weight:700;}
  .inner-head p{font-size:23px;font-weight:700;color:var(--blue);margin-top:12px;}
  .feature{position:absolute;width:280px;}
  .feature-title{font-size:13.5px;font-weight:700;color:var(--blue);padding-left:66px;padding-bottom:3px;}
  .feature-rule{height:1px;background:#b9c2cf;margin-left:66px;width:200px;}
  .feature-body{font-size:10.8px;line-height:12.4px;color:#3b4a5e;padding-left:66px;margin-top:6px;width:270px;}
  .feature-icon{position:absolute;left:8px;top:-6px;width:52px;height:52px;}
</style>
</head>
<body>
<div class="board">

  <svg class="art" width="1736" height="2146" viewBox="0 0 1736 2146" xmlns="http://www.w3.org/2000/svg">
    <defs>
      <linearGradient id="blueSweep" x1="0" y1="0" x2="1" y2="1">
        <stop offset="0" stop-color="#2d92da"/>
        <stop offset="0.55" stop-color="#1f80cd"/>
        <stop offset="1" stop-color="#0a66b8"/>
      </linearGradient>
      <linearGradient id="blueprintTone" x1="0" y1="0" x2="1" y2="1">
        <stop offset="0" stop-color="#cfe2f5"/>
        <stop offset="1" stop-color="#a9cbec"/>
      </linearGradient>
      <linearGradient id="wallTone" x1="0" y1="0" x2="1" y2="0">
        <stop offset="0" stop-color="#cfd0cc"/>
        <stop offset="0.6" stop-color="#8f8a80"/>
        <stop offset="1" stop-color="#d9d9d6"/>
      </linearGradient>
      <linearGradient id="kitchenTone" x1="0" y1="0" x2="0" y2="1">
        <stop offset="0" stop-color="#dfe9f1"/>
        <stop offset="0.38" stop-color="#c9a57c"/>
        <stop offset="0.58" stop-color="#e8eef3"/>
        <stop offset="0.72" stop-color="#3b4a6a"/>
        <stop offset="1" stop-color="#2a2c45"/>
      </linearGradient>
      <linearGradient id="waterTone" x1="0" y1="0" x2="0" y2="1">
        <stop offset="0" stop-color="#46557a"/>
        <stop offset="1" stop-color="#2a2c45"/>
      </linearGradient>
    </defs>

    <!-- cover spread -->
    <rect x="168" y="129" width="1400" height="904" fill="var(--paper)"/>
    <g role="img" aria-label="Photo of rolled architectural blueprints">
      <polygon points="168,129 425,129 745,330 465,515 168,545" fill="url(#blueprintTone)"/>
    </g>
    <polygon points="425,129 1065,129 745,330" fill="var(--paper-deep)"/>
    <g role="img" aria-label="Photo of a gloved hand spreading tile adhesive on a wall with a trowel">
      <polygon points="1065,129 1568,129 1568,460 1380,572 870,255" fill="url(#wallTone)"/>
    </g>
    <polygon points="168,545 300,620 168,685" fill="var(--cyan)"/>
    <polygon points="168,685 465,515 568,578 168,805" fill="var(--navy)"/>
    <polygon points="1568,460 1568,545 1450,560" fill="var(--cyan)"/>
    <polygon points="1330,590 1568,500 1568,685 1495,645" fill="var(--navy)"/>
    <polygon points="465,515 870,255 1495,645 1220,810 1095,735 970,805 568,578" fill="url(#blueSweep)"/>

    <!-- inner spread -->
    <rect x="868" y="1077" width="700" height="906" fill="var(--paper)"/>
    <g role="img" aria-label="Photo of a modern kitchen flooded with water">
      <rect x="168" y="1077" width="700" height="906" fill="url(#kitchenTone)"/>
    </g>
    <polygon points="845,1795 845,1930 730,1860" fill="var(--blue)"/>
    <g role="img" aria-label="Photo of flood water covering a floor">
      <polygon points="868,1720 1035,1627 1568,1860 1568,1983 868,1983" fill="url(#waterTone)"/>
    </g>
    <polygon points="868,1530 1010,1607 868,1695" fill="var(--navy)"/>
  </svg>

  <!-- back panel -->
  <div class="contact">
    <div class="contact-title">Get In Touch</div>
    <div class="contact-rule"><span></span></div>
    <div class="contact-icons">
      <svg viewBox="0 0 22 22" aria-label="Phone"><circle cx="11" cy="11" r="10" fill="var(--blue)"/><path d="M7.5 6.5l2 -.5 1 2.3-1.2 1c.6 1.3 1.6 2.3 2.9 2.9l1-1.2 2.3 1-.5 2c-4 .2-7.7-3.5-7.5-7.5z" fill="#fff"/></svg>
      <svg viewBox="0 0 22 22" aria-label="Website"><circle cx="11" cy="11" r="10" fill="var(--blue)"/><circle cx="11" cy="11" r="5.5" fill="none" stroke="#fff" stroke-width="1.3"/><path d="M5.5 11h11M11 5.5c-2.5 3-2.5 8 0 11M11 5.5c2.5 3 2.5 8 0 11" fill="none" stroke="#fff" stroke-width="1.1"/></svg>
      <svg viewBox="0 0 22 22" aria-label="Location"><circle cx="11" cy="11" r="10" fill="var(--blue)"/><path d="M11 5a4 4 0 0 0-4 4c0 3 4 7.5 4 7.5s4-4.5 4-7.5a4 4 0 0 0-4-4z" fill="#fff"/><circle cx="11" cy="9" r="1.6" fill="var(--blue)"/></svg>
    </div>
    <div class="contact-phone">919.555.0147</div>
    <div class="contact-web">www.<b>Q-J-Restoration</b>.example</div>
    <div class="contact-address">48 Harbor Lane, Riverton, 27601<br>United States</div>
  </div>
  <div class="wordmark wordmark--back"><span class="mark-square"></span>Q&amp;J Restoration</div>

  <!-- front panel -->
  <div class="wordmark wordmark--front"><span class="mark-square"></span>Q&amp;J Restoration</div>
  <div class="front-tagline">INSURANCE CLAIM<br>SPECIALIST</div>
  <div class="front-web">www.<b>Q-J-Restoration</b>.example</div>

  <!-- inner right panel -->
  <div class="inner-head">
    <h2>Has your Business or Home<br>Suffered Water Damage?</h2>
    <p>What happens after the cleanup?</p>
  </div>

  <div class="feature" style="left:932px;top:1311px;">
    <svg class="feature-icon" viewBox="0 0 52 52" aria-hidden="true"><circle cx="26" cy="26" r="24" fill="var(--blue)" stroke="#fff" stroke-width="3"/><path d="M14 20h14v-3h6v9h-4v-3H14z" fill="#fff"/><path d="M31 30c0 0-4 5-4 7a4 4 0 0 0 8 0c0-2-4-7-4-7z" fill="#fff"/></svg>
    <div class="feature-title">Adjuster’s Inspection</div>
    <div class="feature-rule"></div>
    <div class="feature-body">We meet your adjuster on site, document every loss in detail and make sure nothing is missed before the final estimate is written and approved.</div>
  </div>

  <div class="feature" style="left:1238px;top:1311px;">
    <svg class="feature-icon" viewBox="0 0 52 52" aria-hidden="true"><circle cx="26" cy="26" r="24" fill="var(--blue)" stroke="#fff" stroke-width="3"/><path d="M17 14h18M17 38h18M19 14c0 8 6 8 6 12s-6 4-6 12M33 14c0 8-6 8-6 12s6 4 6 12" fill="none" stroke="#fff" stroke-width="2.6" stroke-linecap="round"/><path d="M21 35l5-5 5 5z" fill="#fff"/></svg>
    <div class="feature-title">Timely Settlement</div>
    <div class="feature-rule"></div>
    <div class="feature-body">Clear paperwork and steady follow-up keep your claim moving, so repairs can begin sooner and your home or business is back in use fast.</div>
  </div>

  <div class="feature" style="left:932px;top:1430px;">
    <svg class="feature-icon" viewBox="0 0 52 52" aria-hidden="true"><circle cx="26" cy="26" r="24" fill="var(--blue)" stroke="#fff" stroke-width="3"/><path d="M12 27l14-12 14 12h-4v11H16V27z" fill="#fff"/><rect x="23" y="30" width="6" height="8" fill="var(--blue)"/></svg>
    <div class="feature-title">Under One Roof</div>
    <div class="feature-rule"></div>
    <div class="feature-body">Drying, rebuilding, painting and finishing are handled by one crew, with one point of contact from the first call until the last walkthrough.</div>
  </div>

  <div class="feature" style="left:1238px;top:1430px;">
    <svg class="feature-icon" viewBox="0 0 52 52" aria-hidden="true"><circle cx="26" cy="26" r="24" fill="var(--blue)" stroke="#fff" stroke-width="3"/><path d="M16 36l14-14" stroke="#fff" stroke-width="4" stroke-linecap="round"/><circle cx="32" cy="19" r="5" fill="none" stroke="#fff" stroke-width="3"/><path d="M18 16l18 18" stroke="#fff" stroke-width="4" stroke-linecap="round"/><rect x="14" y="13" width="7" height="5" transform="rotate(45 17.5 15.5)" fill="#fff"/></svg>
    <div class="feature-title">Superior Craftsmanship</div>
    <div class="feature-rule"></div>
    <div class="feature-body">Skilled trades restore walls, floors and cabinets to match the existing finish, and every job is checked twice before we hand back the keys.</div>
  </div>

  <div class="wordmark wordmark--inner"><span class="mark-square"></span>Q&amp;J Restoration</div>

  <!-- board labels -->
  <div class="side-label" style="left:122px;top:975px;">BACK</div>
  <div class="side-label" style="left:1588px;top:962px;">FRONT</div>
  <div class="side-label" style="left:122px;top:1883px;">INNER -01</div>
  <div class="side-label" style="left:1588px;top:1878px;">INNER -02</div>
  <div class="caption">Design Concept QJ Restoration Brochure -01</div>

</div>
</body>
</html>
```